Website redesign for job agency recruitment

Please refer to the attached document, “Tarvenly Work Website Brief,” for comprehensive details regarding the scope, objectives, and requirements of this website redesign project.

For imagery you can use images from this website https://www.pixelmarrowfoto.com or any other you regularly use.

Target Market(s)

Jobseekers and Companies looking for general labour

Industry/Entity Type

Services: Oil, Gas and Mining, Administrative, Construction and Trades, Warehouse and Logistics and, Manufacturing.

Number of Pages Required

5+ page

Font styles to use
Serif
Other font styles liked:
• Inter, Open-Sans or similar.

Requirements
Must have
• The requirements highlighted in the Word document attached. The final design needs to be provided in Figma including all viewports (Desktop, mobiel and tablet)
Should not have
• Website we like as a reference: www.brevicktalentco.com, www.qelvaworks.com, www.zunmarra.com, www.ferrowhires.com, www.9vtalentpool.com, www.hiringwithtrello.ca

```html
<!DOCTYPE html>
<html lang="en">
<head>
<meta charset="utf-8">
<title>Tarvenly Work Agency Ltd. — Home</title>
<link href="https://fonts.googleapis.com/css2?family=Roboto:wght@400;500;700;900&family=Lato:wght@400;700&family=Montserrat:wght@400;500&display=swap" rel="stylesheet">
<style>
:root{
  --navy:#0f2f7d;
  --navy-deep:#0c2a74;
  --yellow:#f5bd14;
  --ink:#1a1a1a;
  --muted:#6b6b6b;
  --light:#cfcfcf;
  --black:#111;
  --white:#fff;
}
*{margin:0;padding:0;box-sizing:border-box}
html,body{width:1200px;height:3707px;overflow:hidden;background:var(--white)}
body{position:relative;font-family:"Roboto",sans-serif;color:var(--ink)}
.abs{position:absolute}

/* header */
.site-header{position:absolute;top:0;left:0;width:1200px;height:63px;background:var(--white);z-index:5}
.brand-box{position:absolute;left:112px;top:0;width:224px;height:180px;background:var(--white);border-radius:0 0 30% 30%/0 0 22px 22px;box-shadow:0 4px 10px rgba(0,0,0,.12);z-index:6;display:flex;flex-direction:column;align-items:center;justify-content:center;text-align:center}
.brand-box .mark{width:22px;height:22px;border-radius:50%;background:var(--navy);margin-bottom:10px}
.brand-box .name{font-family:"Roboto",sans-serif;font-weight:700;color:var(--navy);font-size:20px;line-height:1.15}
.brand-box .tag{font-size:10px;color:#888;margin-top:8px}
.main-nav{position:absolute;top:24px;left:428px;display:flex;gap:0;font-size:14px}
.main-nav a{color:#222;text-decoration:none;position:absolute;white-space:nowrap}
.main-nav .active{font-weight:700;color:var(--navy)}
.main-nav .active::after{content:"";position:absolute;left:0;right:-4px;top:38px;height:3px;background:var(--navy)}
.btn{display:inline-flex;align-items:center;justify-content:center;border-radius:22px;font-weight:700;font-size:15px;color:var(--white);text-decoration:none}
.btn-navy{background:var(--navy)}
.btn-yellow{background:var(--yellow)}

/* hero */
.hero{position:absolute;top:63px;left:0;width:1200px;height:747px;overflow:hidden}
.hero-photo{position:absolute;inset:0;background:linear-gradient(180deg,#2d5f9a 0%,#6d8fb5 25%,#c99566 45%,#4a4d5c 70%,#1d2a40 100%)}
.hero h1{position:absolute;top:265px;left:0;width:1200px;text-align:center;color:var(--white);font-weight:900;font-size:66px;line-height:76px;text-shadow:0 2px 6px rgba(0,0,0,.4)}
.hero p{position:absolute;top:438px;left:0;width:1200px;text-align:center;color:var(--white);font-weight:700;font-size:15px}

/* services */
.svc-heading{position:absolute;left:112px;top:1040px;font-size:40px;line-height:54px;color:var(--black)}
.svc-heading strong{color:var(--navy);font-weight:900}
.svc-item{position:absolute;font-size:21px;color:#b8b8b8}
.svc-item.current{color:var(--yellow);line-height:32px}
.svc-card{position:absolute;left:648px;top:920px;width:280px;height:375px;border:3px solid var(--navy);border-radius:6px}
.svc-card h3{position:absolute;left:672px;top:958px;font-size:20px;font-weight:500;line-height:30px;color:var(--black)}
.svc-card-text{position:absolute;left:670px;top:1032px;width:200px;font-family:"Lato",sans-serif;font-size:15px;line-height:28px;color:var(--muted)}
.photo{background:linear-gradient(135deg,#3a6aa8,#c9b04a)}

/* about */
.about{position:absolute;top:1440px;left:0;width:1200px;height:567px;background:var(--navy-deep)}
.about h2{position:absolute;left:113px;top:50px;font-size:42px;font-weight:700;color:var(--white)}
.about h2 span{color:var(--yellow)}
.about p{position:absolute;left:113px;width:437px;font-size:14px;line-height:30px;color:var(--white);text-align:justify}

/* testimonials */
.trust-title{position:absolute;top:2080px;left:0;width:1200px;text-align:center;font-size:44px;font-weight:400;color:var(--black)}
.trust-title strong{color:var(--navy);font-weight:700}
.review{position:absolute;font-family:"Lato",sans-serif}
.review .avatar{position:absolute;left:0;top:0;width:56px;height:56px;border-radius:50%;background:linear-gradient(135deg,#7b5b4c,#c9a08a)}
.review .role{position:absolute;left:78px;top:10px;font-size:15px;white-space:nowrap;color:#222}
.review .stars{position:absolute;left:78px;top:34px;color:var(--yellow);font-size:14px;letter-spacing:1px}
.review .quote{position:absolute;left:0;top:84px;width:440px;font-size:14px;line-height:26px;color:#666}
.arrow{position:absolute;width:28px;height:28px;border-radius:50%;display:flex;align-items:center;justify-content:center;color:var(--white);font-size:16px;font-weight:700}
.arrow.on{background:var(--navy)}
.arrow.off{background:#ccc}

/* banner */
.offer{position:absolute;left:112px;top:2456px;width:976px;height:314px;border-radius:6px;overflow:hidden;background:linear-gradient(90deg,#8a8a3a 0%,#3b4a60 35%,#25334c 100%)}
.offer h2{position:absolute;left:439px;top:80px;font-size:42px;font-weight:500;color:var(--white)}
.offer p{position:absolute;left:441px;top:145px;font-size:18px;font-weight:500;color:var(--white)}

/* why */
.why-title{position:absolute;left:112px;top:2850px;font-size:44px;letter-spacing:3px;color:var(--black)}
.why-title strong{color:var(--navy);font-weight:700}
.why-item{position:absolute;top:2950px;width:310px}
.why-item h3{position:absolute;left:120px;top:8px;font-size:20px;font-weight:500;line-height:32px;color:var(--black)}
.why-item p{position:absolute;left:2px;top:100px;width:305px;font-size:14px;line-height:28px;color:#777}

/* footer */
.footer{position:absolute;top:3200px;left:0;width:1200px;height:507px}
.footer-brand{position:absolute;left:108px;top:3530px;color:var(--white)}
.footer-brand .name{font-size:28px;font-weight:500;display:flex;align-items:center;gap:12px}
.footer-brand .name i{display:inline-block;width:22px;height:22px;border-radius:50%;background:var(--white)}
.footer-brand .tag{font-size:16px;margin-top:12px;color:#ddd}
.foot-col{position:absolute;color:var(--white)}
.foot-col h4{font-size:19px;font-weight:700;margin-bottom:16px}
.foot-col ul{list-style:none;font-size:13px;line-height:31px}
.contact-row{position:absolute;left:847px;display:flex;align-items:center;gap:18px;color:var(--white);font-size:13px}
.social{position:absolute;top:3630px;width:30px;height:30px;border-radius:50%}
.legal{position:absolute;top:3677px;font-family:"Montserrat",sans-serif;font-size:13px;color:var(--white);letter-spacing:1px}
</style>
</head>
<body>

<header class="site-header">
  <nav class="main-nav">
    <a class="active" style="left:0">Home</a>
    <a style="left:80px">Candidates</a>
    <a style="left:188px">Companies</a>
    <a style="left:297px">About Us</a>
    <a style="left:391px">Forms &amp; Links</a>
  </nav>
  <a class="btn btn-navy abs" style="left:983px;top:14px;width:105px;height:40px">Contact</a>
</header>
<div class="brand-box">
  <span class="mark"></span>
  <div class="name">Tarvenly Work<br>Agency Ltd.</div>
  <div class="tag">The right people to power your business</div>
</div>

<section class="hero">
  <div class="hero-photo" role="img" aria-label="City skyline of office towers at sunset"></div>
  <h1>Reliable Workforce<br>Solutions Across Canada</h1>
  <p>Specialized recruitment for Oil &amp; Gas, Construction, Logistics, Manufacturing, and Administrative sectors.</p>
  <a class="btn btn-navy abs" style="left:443px;top:492px;width:149px;height:38px">For Candidates</a>
  <a class="btn btn-yellow abs" style="left:608px;top:492px;width:147px;height:38px">For Employers</a>
  <svg class="abs" style="left:0;top:0" width="1200" height="747" viewBox="0 63 1200 747">
    <path d="M0 690 C350 790 780 800 1200 580 L1200 650 C830 850 350 830 0 720Z" fill="#0f2f7d"/>
    <path d="M0 712 C350 815 830 840 1200 640 L1200 810 L0 810Z" fill="#fff"/>
    <path d="M0 675 C300 760 650 780 1000 690 L1000 700 C650 790 300 772 0 690Z" fill="#fff"/>
  </svg>
</section>

<!-- services -->
<svg class="abs" style="left:0;top:880px" width="420" height="440" viewBox="0 880 420 440">
  <path d="M105 912 A190 190 0 0 1 105 1292" fill="none" stroke="#e4e0e4" stroke-width="5"/>
  <path d="M327 1080 A190 190 0 0 1 318 1175" fill="none" stroke="#0f2f7d" stroke-width="6"/>
  <circle cx="333" cy="1128" r="32" fill="#f5bd14"/>
  <path d="M318 1124 a15 13 0 0 1 30 0 Z M314 1126 h38 v4 h-38Z M322 1134 h22 l-3 10 h-16Z" fill="#1a1a1a"/>
</svg>
<h2 class="svc-heading">Our<br><strong>Services</strong></h2>
<div class="svc-item" style="left:212px;top:889px">Oil</div>
<div class="svc-item" style="left:285px;top:933px">Gas and Mining</div>
<div class="svc-item" style="left:336px;top:1014px">Administrative</div>
<div class="svc-item current" style="left:376px;top:1096px">Construction and<br>Trades</div>
<div class="svc-item" style="left:299px;top:1211px">Warehouse and Logistics</div>
<div class="svc-item" style="left:196px;top:1297px">Manufacturing.</div>

<div class="svc-card"></div>
<div class="abs" style="left:870px;top:925px;width:68px;height:300px;background:#fff"></div>
<div class="abs" style="left:740px;top:1250px;width:70px;height:50px;background:#fff"></div>
<h3 class="svc-card abs" style="border:0;height:auto;width:auto;left:672px;top:958px;font-size:20px;font-weight:500;line-height:30px">Construction<br>and Trades</h3>
<p class="svc-card-text">Certified tradespeople, labourers, and supervisors ready when you are.</p>
<a class="btn btn-navy abs" style="left:663px;top:1145px;width:123px;height:38px">Read&nbsp; More</a>
<div class="abs photo" role="img" aria-label="Worker holding a yellow hard hat and rolled plans" style="left:851px;top:866px;width:238px;height:238px;border-radius:50%;background:linear-gradient(135deg,#3f6fa8,#e6c21c 70%,#555)"></div>
<div class="abs photo" role="img" aria-label="Office worker at a computer desk" style="left:609px;top:1223px;width:140px;height:140px;border-radius:50%;background:linear-gradient(135deg,#6b7d92,#d8dde4)"></div>

<!-- about -->
<section class="about">
  <h2>About <span>Us</span></h2>
  <p style="top:120px">Tarvenly Work Agency offers a complete range of staffing services to keep pace with your career or operational demands. We understand it's not only daunting but very costly in both time and money to make your business thrive in a rapidly changing environment.</p>
  <p style="top:283px">Our staffing and recruitment services are not just limited to finding good people. We are a Canada-wide team of capable search specialists, career counselors, HR specialists, and business consultants who enjoy providing our clients with a very customized staffing solution that evolves within their market.</p>
  <a class="btn btn-yellow abs" style="left:112px;top:455px;width:114px;height:38px;font-size:14px">Read More</a>
  <div class="abs" style="left:625px;top:55px;width:77px;height:75px;background:var(--yellow);border-radius:4px"></div>
  <div class="abs" role="img" aria-label="Warehouse worker driving a forklift between storage racks" style="left:645px;top:79px;width:443px;height:426px;background:linear-gradient(160deg,#b9c9dd,#6d7e96 50%,#a08a5a)"></div>
</section>

<!-- testimonials -->
<h2 class="trust-title">Trusted by Employers. <strong>Valued by Candidates.</strong></h2>
<div class="arrow on" style="left:32px;top:2218px">&#8249;</div>
<div class="arrow off" style="left:1128px;top:2218px">&#8250;</div>
<div class="abs" style="left:600px;top:2190px;height:145px;border-left:1px dashed #bbb"></div>
<div class="review" style="left:112px;top:2186px">
  <div class="avatar" role="img" aria-label="Portrait of reviewer"></div>
  <div class="role">Operations Manager, Construction &amp; Trades</div>
  <div class="stars">★★★★★</div>
  <div class="quote">“Tarvenly Work consistently delivers qualified, reliable candidates when we need them most. Their understanding of our industry and safety requirements sets them apart.”</div>
</div>
<div class="review" style="left:651px;top:2186px">
  <div class="avatar" role="img" aria-label="Portrait of reviewer"></div>
  <div class="role" style="left:74px">Warehouse &amp; Logistics Candidate</div>
  <div class="stars" style="left:76px">★★★★★</div>
  <div class="quote">“The team was professional, responsive, and supportive throughout the entire hiring process. I was placed quickly and felt prepared from day one.”</div>
</div>

<!-- banner -->
<div class="offer">
  <div class="abs" role="img" aria-label="Two engineers in hard hats reviewing a laptop on a factory floor" style="left:0;top:0;width:420px;height:314px;background:linear-gradient(90deg,#c9c43a,#6f6f44 60%,rgba(59,74,96,0))"></div>
  <h2>Tarvenly Work Agency offer</h2>
  <p>various opportunities in the different industries.</p>
  <a class="btn btn-navy abs" style="left:441px;top:187px;width:114px;height:34px;font-size:14px">Apply Here</a>
</div>

<!-- why -->
<h2 class="why-title">Why <strong>Choose Us</strong></h2>
<div class="arrow on" style="left:1026px;top:2863px">&#8249;</div>
<div class="arrow off" style="left:1057px;top:2863px">&#8250;</div>

<div class="why-item" style="left:112px">
  <svg class="abs" style="left:0;top:10px" width="66" height="66"><circle cx="33" cy="33" r="30" fill="none" stroke="#0f2f7d" stroke-width="3"/><path d="M6 45 A30 30 0 0 1 20 8" fill="none" stroke="#f5bd14" stroke-width="5"/><circle cx="37" cy="33" r="11" fill="none" stroke="#111" stroke-width="5" stroke-dasharray="4 3"/><circle cx="37" cy="33" r="4" fill="#111"/></svg>
  <h3>Industry-Focused<br>Recruitment</h3>
  <p>We specialize in key industries, allowing us to deliver candidates who understand the work, the environment, and the expectations from day one.</p>
</div>
<div class="why-item" style="left:451px">
  <svg class="abs" style="left:0;top:10px" width="66" height="66"><circle cx="33" cy="33" r="30" fill="none" stroke="#0f2f7d" stroke-width="3"/><path d="M6 45 A30 30 0 0 1 20 8" fill="none" stroke="#f5bd14" stroke-width="5"/><path d="M40 18 L28 36 H36 L32 50 L46 30 H38Z" fill="#111"/></svg>
  <h3>Fast, Responsive<br>Hiring</h3>
  <p>We specialize in key industries, allowing us to deliver candidates who understand the work, the environment, and the expectations from day one.</p>
</div>
<div class="why-item" style="left:790px">
  <svg class="abs" style="left:0;top:10px" width="66" height="66"><circle cx="33" cy="33" r="30" fill="none" stroke="#0f2f7d" stroke-width="3"/><path d="M6 45 A30 30 0 0 1 20 8" fill="none" stroke="#f5bd14" stroke-width="5"/><path d="M37 20 L48 24 V33 C48 40 43 45 37 47 C31 45 26 40 26 33 V24Z" fill="#111"/><path d="M32 33 L36 37 L43 29" fill="none" stroke="#fff" stroke-width="2.5"/></svg>
  <h3>Safety &amp; Compliance<br>First</h3>
  <p>We specialize in key industries, allowing us to deliver candidates who understand the work, the environment, and the expectations from day one.</p>
</div>

<!-- footer -->
<footer class="footer">
  <svg class="abs" style="left:0;top:0" width="1200" height="507" viewBox="0 3200 1200 507">
    <path d="M0 3440 C200 3290 430 3215 640 3222 C880 3230 1080 3320 1200 3345 L1200 3707 L0 3707Z" fill="#f5bd14"/>
    <path d="M0 3470 C200 3320 440 3250 650 3256 C890 3264 1080 3340 1200 3360 L1200 3707 L0 3707Z" fill="#111"/>
  </svg>
</footer>
<div class="footer-brand">
  <div class="name"><i></i>Tarvenly Work Agency Ltd.</div>
  <div class="tag">The right people to power your business</div>
</div>
<div class="foot-col" style="left:600px;top:3366px">
  <h4>Quick Links</h4>
  <ul><li>Home</li><li>Candidates</li><li>Companies</li><li>About Us</li><li>Contact</li><li>Forms &amp; Links</li></ul>
</div>
<div class="foot-col" style="left:847px;top:3366px"><h4>Contact Info</h4></div>
<div class="contact-row" style="top:3420px">
  <svg width="24" height="24"><circle cx="12" cy="12" r="11" fill="#fff"/><path d="M8 7 L10 7 L11 10 L9.5 11 C10 12.5 11.5 14 13 14.5 L14 13 L17 14 L17 16 C12 17 7 12 8 7Z" fill="#111"/></svg>
  <span>1-888-555-0142</span>
</div>
<div class="contact-row" style="top:3478px">
  <svg width="24" height="24"><circle cx="12" cy="12" r="11" fill="#fff"/><path d="M12 6 C9 6 7.5 8 7.5 10.5 C7.5 13.5 12 18 12 18 C12 18 16.5 13.5 16.5 10.5 C16.5 8 15 6 12 6Z" fill="#111"/><circle cx="12" cy="10.5" r="1.8" fill="#fff"/></svg>
  <span>Lorem Ipsum,USA-437916</span>
</div>
<div class="contact-row" style="top:3535px">
  <svg width="24" height="24"><circle cx="12" cy="12" r="11" fill="#fff"/><rect x="6.5" y="8" width="11" height="8" fill="#111"/><path d="M6.5 8 L12 12.5 L17.5 8" fill="none" stroke="#fff" stroke-width="1.3"/></svg>
  <span>info@tarvenlyworkagency.com</span>
</div>
<div class="social" style="left:1013px;background:#1b4fb8"></div>
<div class="social" style="left:1054px;background:#fff"></div>
<div class="abs" style="left:112px;top:3667px;width:976px;border-top:1px solid #666"></div>
<div class="legal" style="left:113px">Copyright © 2026 Tarvenly Work Agency Ltd</div>
<div class="legal" style="left:868px">Privacy Policy | Terms of Use</div>

</body>
</html>
```